Beauty Salon Mentor Illustration

Hi There, I'm Belinda and I'm a Beauty Salon owner mentor. We are needing 5 different illustration design for a beauty salon coaching business. The pictures will be used on our website next to a small description about our course out line.
Course and what the illustrations will be referring to below:
1. Launch Pad Parlour -Make your dream of owning a salon a reality.
Three options of start-up training and support, teaching must-know insights for beauty therapists who are ready to take the leap to salon owner and want to do it right. Whether you’ve been in the beauty industry a short time or forever, Launch Pad Parlour will set you up for salon success.

2. Chairs Filled Fast - Attract more clients with simple, strategic digital marketing. Chairs Filled Fast educates on the ins and outs of sponsored social media ads. With easy-to-follow video training, you’ll establish your online presence and increase salon bookings.
Learn how to show up on social media with effective strategies that work. Choose our Handled Entirely system, or learn to do it all with our DIY system.

3. Momentum Studio Plan - Transform your salon and your life. Our most tailored program, Momentum Studio Plan offers coaching memberships with Bloom Beauty Hub’s Founder- Belinda. With our results focused framework, you will upskill employees, improve the working environment of the salon and receive leading beauty industry training as we dive into the culture and mindset of your salon. With Belinda as your business mentor and biggest cheerleader get ready to achieve your business goals and move forward with rapid growth.

4. Revive Parlour Path - Successfully put your salon back on the map.
Step into today’s beauty landscape with optimised marketing and industry expertise. If your salon’s been open for a year or even twenty years, Revive Parlour Path will elevate your business, renew your love for your salon and set you up to generate more income. Stand out from the competition as you increase online presence, learn key business development processes and see real results.

5. Skillset Studio Plan - Successfully Upskill and Level Up Your Salon. Skillset Studio Plan offers three training options- In Salon, Online & Diploma of Beauty Therapy. Whether you have your own salon or want to become qualified, Bloom Beauty Hub’s- Skillset Studio Plan adds industry authority and brings specialist expertise to all level of beauty therapists.
Our coaching is based in Australia, aim at female beauty salon owners who are ready to take their business to the next level.

In the files below is just a picture of me so you know who i am. We are wanting the illusion to appeal to a wide audience.

I am the business and everyone i attract into our coaching program works closely with me.

Target Market(s)

Beauty Salon owners; women

Font styles to use
Sans Serif

Colors
fce8d3
fee3d4
fff5ef
fff3d1
f9bb94
fcca95

Requirements
Must have
• Must be relatable to the brief, designs must look great together on the website or separately on their own.
Nice to have
• Industry relatable, engaging to the eye.
Should not have
• i would prefer if there wasn't any words on the illusion

```html
<!DOCTYPE html>
<html lang="en">
<head>
<meta charset="utf-8">
<title>Bloom Beauty Hub – Mobile Pages</title>
<link rel="stylesheet" href="https://fonts.googleapis.com/css2?family=Playfair+Display:ital,wght@0,400;1,400&family=Raleway:wght@400;500&display=swap">
<style>
  :root {
    --backdrop: #f2e4dc;
    --screen-white: #ffffff;
    --top-strip: #fcf3ee;
    --blush-band: #e9d2c2;
    --stone: #ddd3c7;
    --stone-light: #ece4da;
    --petal: #f6f1ec;
    --skin: #e8c4a6;
    --hair: #b59c83;
    --ink: #1f1b19;
    --soft-ink: #2b2522;
    --hero-title: #ffffff;
    --ring: #ffffff;
  }
  * { box-sizing: border-box; margin: 0; padding: 0; }
  html, body { width: 1200px; height: 1200px; overflow: hidden; }
  body { background: var(--backdrop); position: relative; }

  .screen {
    position: absolute;
    top: 114px;
    width: 452px;
    height: 977px;
    background: var(--screen-white);
    border-radius: 36px;
    overflow: hidden;
  }
  .screen--home { left: 88px; }
  .screen--about { left: 669px; }

  /* Home screen */
  .site-header {
    height: 120px;
    position: relative;
  }
  .brand-name {
    position: absolute;
    left: 0;
    right: 0;
    top: 46px;
    text-align: center;
    font-family: "Raleway", sans-serif;
    font-weight: 500;
    font-size: 14px;
    letter-spacing: 1.5px;
    color: var(--ink);
  }
  .menu-toggle {
    position: absolute;
    right: 34px;
    top: 43px;
    width: 32px;
  }
  .menu-toggle span {
    display: block;
    height: 3px;
    background: var(--ink);
    margin-bottom: 9px;
  }
  .hero {
    height: 218px;
    background: var(--blush-band);
    text-align: center;
    padding-top: 52px;
  }
  .hero-title {
    font-family: "Playfair Display", serif;
    font-weight: 400;
    font-size: 38px;
    color: var(--hero-title);
    letter-spacing: 0.5px;
  }
  .hero-tagline {
    font-family: "Playfair Display", serif;
    font-style: italic;
    font-size: 23px;
    line-height: 42px;
    color: var(--soft-ink);
    margin-top: 14px;
  }
  .hero-art {
    height: 452px;
    background:
      radial-gradient(ellipse 34% 46% at 50% 62%, rgba(246,241,236,0.95) 0%, rgba(246,241,236,0.55) 45%, rgba(246,241,236,0) 100%),
      radial-gradient(ellipse 22% 26% at 50% 40%, rgba(232,196,166,0.55) 0%, rgba(232,196,166,0) 100%),
      radial-gradient(ellipse 70% 60% at 50% 45%, var(--stone-light) 0%, var(--stone) 100%);
  }

  /* About screen */
  .top-strip { height: 69px; background: var(--top-strip); }
  .course-intro {
    height: 345px;
    background: var(--blush-band);
    text-align: center;
    padding-top: 20px;
  }
  .course-portrait {
    width: 170px;
    height: 170px;
    margin: 0 auto;
    border-radius: 50%;
    border: 4px solid var(--ring);
    background:
      radial-gradient(ellipse 34% 46% at 50% 66%, rgba(246,241,236,0.95) 0%, rgba(246,241,236,0) 100%),
      radial-gradient(ellipse 22% 26% at 50% 40%, rgba(232,196,166,0.55) 0%, rgba(232,196,166,0) 100%),
      radial-gradient(circle at 50% 45%, var(--stone-light) 0%, #d8cfc3 100%);
  }
  .course-title {
    font-family: "Playfair Display", serif;
    font-weight: 400;
    font-size: 25px;
    color: var(--ink);
    margin-top: 12px;
  }
  .course-text {
    font-family: "Playfair Display", serif;
    font-size: 21px;
    line-height: 35px;
    color: var(--ink);
    margin: 10px 40px 0;
  }
  .about {
    text-align: center;
    padding: 78px 30px 0;
  }
  .about-title {
    font-family: "Playfair Display", serif;
    font-weight: 400;
    font-size: 36px;
    color: var(--ink);
  }
  .about-subtitle {
    font-family: "Playfair Display", serif;
    font-style: italic;
    font-size: 20px;
    color: var(--soft-ink);
    margin-top: 22px;
  }
  .about-text {
    font-family: "Raleway", sans-serif;
    font-size: 18.5px;
    line-height: 37px;
    color: var(--ink);
    margin-top: 24px;
  }
</style>
</head>
<body>

  <section class="screen screen--home">
    <header class="site-header">
      <div class="brand-name">BLOOM BEAUTY HUB</div>
      <div class="menu-toggle" aria-label="Menu"><span></span><span></span><span></span></div>
    </header>
    <div class="hero">
      <h1 class="hero-title">BLOOM BEAUTY HUB</h1>
      <p class="hero-tagline">Education &amp; Business Mentoring for<br>Beauty Salon Owners made simple.</p>
    </div>
    <div class="hero-art" role="img" aria-label="Illustration of a salon owner cutting a ribbon in front of pale leafy branches"></div>
  </section>

  <section class="screen screen--about">
    <div class="top-strip"></div>
    <div class="course-intro">
      <div class="course-portrait" role="img" aria-label="Round illustration of a salon owner cutting a ribbon"></div>
      <h2 class="course-title">LAUNCH PAD PARLOUR</h2>
      <p class="course-text">All the help you need to start you own salon.</p>
    </div>
    <div class="about">
      <h2 class="about-title">ABOUT US</h2>
      <p class="about-subtitle">Bloom Beauty Hub</p>
      <p class="about-text">Hi, we're ‘Bloom Beauty Hub’ and we've generated tens of thousands of dollars in bookings for businesses in the Beauty Industry in as little as two months using Pagebook &amp; Picstream Advertising.</p>
    </div>
  </section>

</body>
</html>
```